Family flag

Looking to develop a family flag design that reflects how long our family has been vacationing at our beach community in North Wildwood NJ.
would like the flag to incorporate the emblem of the City of Gull Harbor.
Family emblem should be collegiate in look and nature (circle insignia with Pellow family name and year family started coming to GHB Beach 1941.
We are thinking of a circle insignia with three divisions in the center; a beach chair, lifeguard chair and sunset or other beachy ideas.

```html
<!DOCTYPE html>
<html lang="en">
<head>
<meta charset="utf-8">
<title>Pellow Family Flag</title>
<link rel="stylesheet" href="https://fonts.googleapis.com/css2?family=Rye&family=Graduate&family=Roboto+Slab:wght@600;700&display=swap">
<style>
  :root {
    --sand: #fcc862;
    --sea: #2782c6;
    --navy: #283178;
    --navy-soft: rgba(40, 49, 120, 0.28);
    --navy-faint: rgba(40, 49, 120, 0.18);
  }
  html, body {
    margin: 0;
    padding: 0;
    overflow: hidden;
    background: #ffffff;
  }
  .flag {
    position: relative;
    width: 1200px;
    height: 600px;
    background: var(--sand);
    overflow: hidden;
  }
  .flag__art {
    position: absolute;
    inset: 0;
    width: 1200px;
    height: 600px;
    display: block;
  }
  .saltire { fill: var(--sea); }
  .city-seal__ring { fill: var(--sand); stroke: var(--navy); stroke-width: 10; }
  .city-seal__name {
    font-family: "Roboto Slab", serif;
    font-weight: 700;
    font-size: 17px;
    fill: var(--navy);
    text-anchor: middle;
  }
  .icon-area { fill: var(--navy-soft); }
  .ornament-area { fill: var(--navy-faint); }
  .family-name {
    font-family: "Rye", serif;
    font-size: 68px;
    fill: var(--navy);
    stroke: var(--sand);
    stroke-width: 8px;
    stroke-linejoin: round;
    paint-order: stroke fill;
  }
  .rule { stroke: var(--navy); stroke-width: 2.5; }
  .beach-name {
    font-family: "Graduate", serif;
    font-size: 44px;
    fill: var(--navy);
    text-anchor: middle;
    letter-spacing: 4px;
  }
  .since-year {
    font-family: "Roboto Slab", serif;
    font-weight: 600;
    font-size: 14px;
    letter-spacing: 1.5px;
    fill: var(--navy);
    text-anchor: middle;
  }
</style>
</head>
<body>
<main class="flag">
  <svg class="flag__art" viewBox="0 0 1200 600" xmlns="http://www.w3.org/2000/svg">
    <defs>
      <path id="family-arc" d="M 290 440 Q 600 280 910 440"/>
    </defs>

    <g class="saltires">
      <polygon class="saltire" points="0,0 1200,527 1200,572 0,43"/>
      <polygon class="saltire" points="1200,0 0,527 0,572 1200,43"/>
    </g>

    <g class="city-seal">
      <circle class="city-seal__ring" cx="600" cy="110" r="88"/>
      <text class="city-seal__name" x="600" y="106">City of</text>
      <text class="city-seal__name" x="600" y="128">Gull Harbor</text>
    </g>

    <rect class="icon-area icon-area--fins" x="72" y="241" width="180" height="171" rx="14"
          role="img" aria-label="Pair of swim fins icon"/>
    <rect class="icon-area icon-area--chair" x="940" y="204" width="201" height="190" rx="14"
          role="img" aria-label="Beach umbrella and lounge chair icon"/>

    <text class="family-name">
      <textPath href="#family-arc" startOffset="50%" text-anchor="middle"
                textLength="560" lengthAdjust="spacingAndGlyphs">Pellow Family</textPath>
    </text>

    <line class="rule" x1="410" y1="440" x2="790" y2="440"/>
    <text class="beach-name" x="600" y="482">GHB BEACH</text>
    <line class="rule" x1="410" y1="493" x2="543" y2="493"/>
    <line class="rule" x1="658" y1="493" x2="790" y2="493"/>
    <text class="since-year" x="600" y="499">Since 1941</text>

    <rect class="ornament-area" x="412" y="506" width="376" height="63" rx="30"
          role="img" aria-label="Scrollwork flourish with a ship's anchor at centre"/>
  </svg>
</main>
</body>
</html>
```